Buch-/E-Book-Cover für Kinderbuch zum spielerischen Umgang zwischen Kind und Hund
Zielgruppe
Die Zielgruppe sind Kinder die lernen möchten mit Ihrem Hund besser zu spielen, verstehen und erziehen. Es ist ein Kinderbuch und das Buch soll dementsprechend 'kinderlicher' gestaltet sein.
Ich habe kein eigenes Konzept für das Cover mir derzeitig überlegt und ich werde die erstellten Cover bei meiner Zielgruppe testen und danach den Gewinner küren.
In diesem Buch handelt sich um ein Sachbuch zum Thema Hundeerziehung für Kinder. Ich möchte Ihnen die Inhaltsangabe, Vorwort und Buchrückseite mitteilen. Das Buch werde ich auf Lesekorb.de veröffentlichen. Außerdem möchte ich Ihnen die 2 größten Konkurrenten vorstellen.
Das Vorwort:
Vorwort
Der Hund ist für das Kind mehr als nur ein vierbeiniger Hausgenosse mit Kuschelfaktor, er ist ein echter Partner zum Spielen und Lernen. Mit den passenden Ideen gestaltet sich der Alltag mit dem Tier richtig spannend. Sowohl Kind als auch Hund entwickeln sich Schritt für Schritt weiter und wachsen immer mehr zusammen. Für Jungen und Mädchen gibt es vielfältige Möglichkeiten, sich mit ihrem Vierbeiner zu beschäftigen. Kreative Rollenspiele gehören ebenso dazu wie das Lernen von Kunststücken, das Training von Intelligenz und Geschicklichkeit und das Basteln schöner Spielsachen. Lassen Sie sich von diesem Buch inspirieren und von den Fähigkeiten Ihrer Kinder und Hunde überraschen!
Gliederung:
Einleitung und Grundlegendes
1. Warum spielen Hunde und Kinder?
Gemeinsamkeiten zwischen Kind und Welpe
Die Vorteile einer engen Hund-Kind-Beziehung
Kind und Hund – das absolute Dream-Team?
Welcher Hund passt zum Kind?
Voraussetzungen für sicheres Spielen
2. Kreative Spiele
Kreative Beschäftigung mit dem Hund – darf das sein?
Rollenspiele mit Hunden
Das richtige Alter für Rollenspiele
Beispiele für typische Rollenspiele im Kindesalter
Tierische Rollenspiele – vom Kind zum Hund
Eigene Kommandos erfi..
Aufgabenstellung
Der Titel vom Buch lautet: Komm zu uns! Wo Kleine den Vierbeiner kennen, führen und mit ihm toben dürfen.
Das sind die 2 größten Konkurrenten https://www.lesekorb.example/titel/4718
https://www.lesekorb.example/titel/5923
Das sind Cover auf dem Englisch sprachigen Markt die ich sehr gut finde
1. https://www.readbasket.example/item/8841
2. https://www.readbasket.example/item/3307

```html
<!DOCTYPE html>
<html lang="de">
<head>
<meta charset="utf-8">
<title>Komm zu uns! – Cover und Vorwort</title>
<link href="https://fonts.googleapis.com/css2?family=Chewy&family=Permanent+Marker&family=Patrick+Hand&display=swap" rel="stylesheet">
<style>
  :root {
    --blue: #3fa7dc;
    --white: #ffffff;
    --paper: #efefef;
    --photo-top: #8a8f94;
    --photo-mid: #4f6f92;
    --photo-low: #7d9cc0;
  }
  * { margin: 0; padding: 0; box-sizing: border-box; }
  html, body { width: 1200px; height: 1200px; overflow: hidden; background: var(--white); }
  .canvas { position: relative; width: 1200px; height: 1200px; background: var(--white); }

  /* Front cover */
  .cover { position: absolute; left: 44px; top: 160px; width: 559px; height: 840px; }
  .cover-title {
    position: absolute; left: 0; top: 0; width: 559px;
    font-family: "Chewy", cursive; color: var(--blue);
    font-size: 112px; line-height: 96px; text-align: center;
  }
  .subtitle-band { position: absolute; left: 0; top: 204px; width: 559px; height: 134px; }
  .subtitle-band svg { position: absolute; inset: 0; }
  .subtitle {
    position: absolute; left: 0; top: 18px; width: 559px;
    font-family: "Permanent Marker", cursive; color: var(--white);
    font-size: 25px; line-height: 35px; text-align: center; text-transform: uppercase;
  }
  .cover-photo {
    position: absolute; left: 0; top: 337px; width: 559px; height: 503px;
    background: linear-gradient(180deg, var(--photo-top) 0%, var(--photo-mid) 55%, var(--photo-low) 100%);
  }

  /* Foreword page */
  .foreword { position: absolute; left: 630px; top: 152px; width: 548px; height: 845px; }
  .foreword > svg { position: absolute; inset: 0; }
  .foreword-title {
    position: absolute; left: 0; top: 38px; width: 548px;
    font-family: "Chewy", cursive; color: var(--white);
    font-size: 66px; text-align: center;
  }
  .foreword-sheet {
    position: absolute; left: 56px; top: 154px; width: 437px; height: 622px;
    background: linear-gradient(135deg, #f6f6f6 0%, var(--paper) 50%, #e6e6e6 100%);
    padding: 20px 18px 0;
  }
  .foreword-text {
    font-family: "Patrick Hand", cursive; color: var(--blue);
    font-size: 20.5px; line-height: 29.6px; text-align: center; font-weight: 700;
    letter-spacing: 0.1px;
  }
</style>
</head>
<body>
<main class="canvas">

  <section class="cover">
    <h1 class="cover-title">Komm<br>zu uns!</h1>

    <div class="subtitle-band">
      <svg width="559" height="134" viewBox="0 0 559 134" aria-hidden="true">
        <path fill="#3fa7dc" d="M0 16 L60 10 L200 8 L360 4 L559 0 L559 110 L520 112 L430 116 L330 122 L230 124 L150 126 L60 128 L0 134 L0 112 L110 106 L0 100 L0 60 L90 58 L0 50 Z"/>
        <path fill="#ffffff" d="M0 44 L85 46 L84 49 L0 50 Z"/>
        <path fill="#ffffff" d="M0 98 L100 98 L108 102 L0 104 Z"/>
        <path fill="#ffffff" d="M350 122 L559 108 L559 112 L360 126 Z"/>
      </svg>
      <p class="subtitle">Wo Kleine den Vierbeiner<br>kennen, führen und mit ihm<br>toben dürfen</p>
    </div>

    <div class="cover-photo" role="img" aria-label="Foto: Ein Junge sitzt auf einer Treppe und zeigt seinem Corgi einen bunten Spielball"></div>
  </section>

  <section class="foreword">
    <svg width="548" height="845" viewBox="0 0 548 845" aria-hidden="true">
      <rect width="548" height="845" fill="#3fa7dc"/>
      <g fill="#ffffff">
        <path d="M0 32 L24 30 L24 36 L0 38 Z"/>
        <path d="M548 52 L492 54 L484 62 L548 66 Z"/>
        <path d="M0 116 L120 122 L190 124 L140 130 L0 140 Z"/>
        <path d="M0 208 L56 210 L56 226 L0 222 Z"/>
        <path d="M548 218 L493 220 L493 234 L548 232 Z"/>
        <path d="M0 295 L56 292 L56 300 L0 304 Z"/>
        <path d="M548 360 L493 364 L493 372 L548 370 Z"/>
        <path d="M0 468 L56 462 L56 470 L0 474 Z"/>
        <path d="M548 460 L493 462 L493 476 L548 472 Z"/>
        <path d="M0 600 L56 596 L56 608 L0 606 Z"/>
        <path d="M548 600 L493 602 L493 612 L548 610 Z"/>
        <path d="M0 670 L56 668 L56 680 L0 684 Z"/>
        <path d="M548 676 L493 676 L493 686 L548 684 Z"/>
        <path d="M0 755 L56 752 L56 764 L0 768 Z"/>
        <path d="M0 780 L90 778 L230 774 L60 786 L0 790 Z"/>
        <path d="M548 820 L500 828 L548 832 Z"/>
      </g>
    </svg>
    <h2 class="foreword-title">Vorwort</h2>
    <div class="foreword-sheet">
      <p class="foreword-text">Der Hund ist für das Kind mehr als nur ein vierbeiniger Hausgenosse mit Kuschelfaktor, er ist ein echter Partner zum Spielen und Lernen. Mit den passenden Ideen gestaltet sich der Alltag mit dem Tier richtig spannend. Sowohl Kind als auch Hund entwickeln sich Schritt für Schritt weiter und wachsen immer mehr zusammen. Für Jungen und Mädchen gibt es vielfältige Möglichkeiten, sich mit ihrem Vierbeiner zu beschäftigen. Kreative Rollenspiele gehören ebenso dazu wie das Lernen von Kunststücken, das Training von Intelligenz und Geschicklichkeit und das Basteln schöner Spielsachen. Lassen Sie sich von diesem Buch inspirieren und von den Fähigkeiten Ihrer Kinder und Hunde überraschen!</p>
    </div>
  </section>

</main>
</body>
</html>
```